OBK Farcoast Logistics Limited

We need the buissnes card to be very exclusive. As we are all young in our company. We need this to be the gate to make our clients feel deep interest for us.

We are focused in as International Trade advisors, and our products go from Oil Tanker Ships to Rubber balls for dogs.

Our Slogan is Making Global Local.
And our main marketing will be through Internet.

We were stablished in 2009 In Mexico and we also have offices in Hong Kong.
We have representatives in China and Europe.

Target Market(s)

Is every company or Individual that wants to develop an International Project or product development or Logistic service of Goods and people.
Some of our current projects are Ship Brokerage, Mine Brokerage, Real State and Product Pormotional development.

Industry/Entity Type

It Company

Requirements
Must have
• Our Logo and slogan, and make the card accoriding to the logo.
Nice to have
• Our Colors

```html
<!DOCTYPE html>
<html lang="en">
<head>
<meta charset="utf-8">
<title>OBK Farcoast Logistics Limited – Business Card</title>
<link href="https://fonts.googleapis.com/css2?family=Source+Sans+3:wght@400;600;700&display=swap" rel="stylesheet">
<style>
  :root {
    --page-bg: #d8d4cf;
    --card-bg: #eee8e1;
    --brand-blue: #1a7db8;
    --brand-green: #7dc242;
    --ink-light: #ffffff;
    --tagline: #4a6b86;
  }
  * { margin: 0; padding: 0; box-sizing: border-box; }
  html, body {
    width: 1200px;
    height: 905px;
    overflow: hidden;
    background: var(--page-bg);
    font-family: "Source Sans 3", "Helvetica Neue", Arial, sans-serif;
  }
  .card {
    position: absolute;
    left: 100px;
    top: 168px;
    width: 1000px;
    height: 568px;
    background: var(--card-bg);
    overflow: hidden;
    box-shadow: 0 6px 18px rgba(0,0,0,0.12);
  }
  .card-shapes { position: absolute; inset: 0; }
  .brand {
    position: absolute;
    left: 0;
    width: 974px;
    top: 170px;
    display: flex;
    justify-content: center;
    align-items: center;
    gap: 18px;
  }
  .brand-dot {
    width: 34px;
    height: 34px;
    border-radius: 50%;
    background: var(--brand-blue);
  }
  .brand-name {
    font-size: 82px;
    font-weight: 700;
    line-height: 1;
    color: var(--brand-green);
    letter-spacing: 4px;
  }
  .brand-tagline, .brand-slogan {
    position: absolute;
    left: 0;
    width: 974px;
    text-align: center;
    color: var(--tagline);
  }
  .brand-tagline { top: 262px; font-size: 15px; letter-spacing: 0.5px; }
  .brand-slogan { top: 288px; font-size: 19px; font-weight: 600; letter-spacing: 1px; }
  .person {
    position: absolute;
    right: 547px;
    top: 399px;
    text-align: right;
    color: var(--ink-light);
  }
  .person-name { font-size: 30px; font-weight: 700; line-height: 38px; }
  .person-role, .person-address { font-size: 25px; font-weight: 400; line-height: 38px; }
  .divider {
    position: absolute;
    left: 477px;
    top: 404px;
    width: 2px;
    height: 142px;
    background: rgba(255,255,255,0.55);
  }
  .contacts {
    position: absolute;
    left: 502px;
    top: 399px;
    list-style: none;
    color: var(--ink-light);
  }
  .contact {
    display: flex;
    align-items: center;
    gap: 12px;
    font-size: 25px;
    line-height: 38px;
  }
  .contact-icon { width: 22px; height: 22px; flex: none; }
</style>
</head>
<body>
  <div class="card">
    <svg class="card-shapes" width="1000" height="568" viewBox="0 0 1000 568" aria-hidden="true">
      <path class="accent-arc" d="M40,470 Q500,232 960,480 L960,492 Q500,262 40,480 Z" fill="var(--brand-green)"/>
      <path class="info-band" d="M0,486 Q500,250 1000,480 L1000,568 L0,568 Z" fill="var(--brand-blue)"/>
    </svg>

    <div class="brand">
      <span class="brand-dot"></span>
      <span class="brand-name">OBK</span>
    </div>
    <p class="brand-tagline">OBK Farcoast Logistics Limited</p>
    <p class="brand-slogan">Making Global Local</p>

    <div class="person">
      <p class="person-name">Your Name</p>
      <p class="person-role">Position</p>
      <p class="person-address">00, Complex Name<br>City, State, 00045</p>
    </div>

    <div class="divider"></div>

    <ul class="contacts">
      <li class="contact">
        <svg class="contact-icon" viewBox="0 0 24 24"><path d="M6.6 2.5l3 3.2-1.8 2.6c1 2.3 3.5 4.9 5.9 5.9l2.6-1.8 3.2 3-1.6 3.6C11 19 5 13 3 6.1z" fill="#fff"/></svg>
        <span>123-456-7890</span>
      </li>
      <li class="contact">
        <svg class="contact-icon" viewBox="0 0 24 24"><rect x="6" y="1.5" width="12" height="21" rx="2" fill="#fff"/><rect x="8" y="4.5" width="8" height="10" fill="var(--brand-blue)"/><circle cx="12" cy="18.5" r="1.5" fill="var(--brand-blue)"/></svg>
        <span>123-456-7890</span>
      </li>
      <li class="contact">
        <svg class="contact-icon" viewBox="0 0 24 24"><rect x="2" y="6" width="20" height="13" rx="1.5" fill="#fff"/><path d="M3 7l9 7 9-7" fill="none" stroke="var(--brand-blue)" stroke-width="1.8"/></svg>
        <span>info@obkfarcoast.com</span>
      </li>
      <li class="contact">
        <svg class="contact-icon" viewBox="0 0 24 24" fill="none" stroke="#fff" stroke-width="1.8"><circle cx="12" cy="12" r="9.5"/><ellipse cx="12" cy="12" rx="4" ry="9.5"/><path d="M2.5 12h19M4 7h16M4 17h16"/></svg>
        <span>www.obkfarcoast.com</span>
      </li>
    </ul>
  </div>
</body>
</html>
```